Process Serving Company needs a letterhead design

Looking to have a letterhead designed for letters to attorneys advertising our business. We would like something eye catching but professional. Colors and logos are attached. Please add "Process Service and Attorney Support" near the logo or header

Target Market(s)

Attorneys

Font styles to use
Serif
Sans Serif

Colors
33a6d7
0255a3
85cae6
cee9f5
ecf7fb

```html
<!DOCTYPE html>
<html lang="en">
<head>
<meta charset="utf-8">
<title>Halvorsen Legal Courier Letterhead</title>
<link href="https://fonts.googleapis.com/css2?family=PT+Sans:wght@400;700&family=Arimo:wght@700&display=swap" rel="stylesheet">
<style>
  :root {
    --brand-blue: #0091d3;
    --brand-navy: #0255a3;
    --brand-sky: #85cae6;
    --brand-link: #33a6d7;
    --paper: #fafafa;
    --backdrop: #e6e6e6;
    --ink: #333333;
    --ink-soft: #444444;
    --white: #ffffff;
  }
  * { margin: 0; padding: 0; box-sizing: border-box; }
  html, body {
    width: 1059px;
    height: 1200px;
    overflow: hidden;
    background: var(--backdrop);
  }
  .letterhead {
    position: absolute;
    left: 105px;
    top: 0;
    width: 849px;
    height: 1200px;
    background: var(--paper);
    font-family: "PT Sans", sans-serif;
    color: var(--ink);
    overflow: hidden;
  }
  .header-band {
    position: absolute;
    left: 0;
    top: 0;
    width: 849px;
    height: 130px;
  }
  .brand {
    position: absolute;
    left: 40px;
    top: 22px;
    display: flex;
    align-items: center;
    gap: 14px;
  }
  .brand-mark {
    width: 44px;
    height: 44px;
    border: 2px solid var(--white);
  }
  .brand-name {
    font-family: "PT Sans", sans-serif;
    font-weight: 400;
    font-size: 28px;
    line-height: 1;
    color: var(--white);
    letter-spacing: 0.5px;
  }
  .contact {
    position: absolute;
    top: 112px;
    font-size: 12.5px;
    line-height: 15.5px;
    color: var(--ink);
  }
  .contact-lines { left: 482px; }
  .contact-lines li {
    list-style: none;
    display: flex;
    align-items: center;
    gap: 5px;
  }
  .contact-lines svg { width: 10px; height: 10px; flex: none; }
  .contact-address { left: 640px; font-size: 11.5px; font-style: normal; }
  .contact-address .web { color: var(--brand-link); font-size: 12.5px; }
  .letter-body {
    position: absolute;
    left: 72px;
    top: 267px;
    width: 711px;
  }
  .salutation {
    font-family: "Arimo", sans-serif;
    font-weight: 700;
    font-size: 18px;
    color: var(--ink-soft);
    margin-bottom: 40px;
  }
  .letter-body p {
    font-size: 15.4px;
    line-height: 22px;
    margin-bottom: 22px;
  }
  .signature {
    position: absolute;
    left: 72px;
    top: 866px;
    width: 138px;
    height: 66px;
    background: linear-gradient(90deg, #e4e4e4, #eeeeee);
  }
</style>
</head>
<body>
  <main class="letterhead">
    <svg class="header-band" viewBox="0 0 849 130" preserveAspectRatio="none" aria-hidden="true">
      <path d="M0,0 H849 V72 L0,92 Z" fill="var(--brand-blue)"/>
      <path d="M0,97 L849,77" stroke="var(--brand-navy)" stroke-width="4"/>
      <path d="M420,96 L849,86" stroke="var(--brand-sky)" stroke-width="2"/>
    </svg>

    <div class="brand">
      <div class="brand-mark"></div>
      <div class="brand-name">HALVORSEN LEGAL COURIER</div>
    </div>

    <ul class="contact contact-lines">
      <li>
        <svg viewBox="0 0 10 10"><path d="M2,0.5 L3.6,2.6 L2.8,3.6 C3.4,5 4.8,6.4 6.2,7 L7.2,6.2 L9.4,7.8 L8.4,9.4 C4.4,9 1,5.6 0.6,1.6 Z" fill="var(--brand-link)"/></svg>
        555-201-4410
      </li>
      <li>
        <svg viewBox="0 0 10 10"><rect x="0.5" y="3" width="9" height="5" rx="1" fill="var(--brand-link)"/><rect x="2" y="1" width="6" height="3" fill="var(--brand-link)"/><rect x="2.5" y="5" width="5" height="1" fill="var(--white)"/></svg>
        555-201-4411
      </li>
      <li>
        <svg viewBox="0 0 10 10"><circle cx="5" cy="5" r="4.2" fill="none" stroke="var(--brand-link)" stroke-width="1.2"/><path d="M0.8,5 H9.2 M5,0.8 V9.2" stroke="var(--brand-link)" stroke-width="1"/></svg>
        info@halvorsenlegal.com
      </li>
    </ul>

    <address class="contact contact-address">
      2150 W Canyon Rd #48<br>
      Mesa Ridge AZ 85001<br>
      <span class="web">www.halvorsenlegal.com</span>
    </address>

    <section class="letter-body">
      <h1 class="salutation">Dear Mr. John,</h1>
      <p>Lorem Ipsum is simply dummy text of the printing and typesetting industry. Lorem Ipsum has been the industry's standard dummy text ever since the 1500s, when an unknown printer took a galley of type and scrambled it to make a type specimen book. It has survived not only five centuries, but also the leap into electronic typesetting, remaining essentially unchanged.</p>
      <p>The standard chunk of Lorem Ipsum used since the 1500s is reproduced below for those interested. Sections 1.10.32 and 1.10.33 of the old source text are also reproduced in their exact original form, accompanied by English versions from a later printed translation.</p>
      <p>Lorem Ipsum is simply dummy text of the printing and typesetting industry. Lorem Ipsum has been the industry's standard dummy text ever since the 1500s, when an unknown printer took a galley of type and scrambled it to make a type specimen book. It has survived not only five centuries, but also the leap into electronic typesetting, remaining essentially unchanged. It was popularised in the</p>
      <p>Lorem Ipsum has been the industry's standard dummy text ever since the 1500s, when an unknown printer took a galley of type and scrambled it to make a type specimen book. It has survived not only five centuries, but also the leap into electronic typesetting, remaining essentially unchanged. It was popularised in the</p>
      <p>Lorem Ipsum is simply dummy text of the printing and typesetting industry. Lorem Ipsum has been the industry's standard dummy text ever since the 1500s, when an unknown printer took a galley of type and scrambled it to make a type specimen book.</p>
    </section>

    <div class="signature" role="img" aria-label="Handwritten signature of the sender"></div>
  </main>
</body>
</html>
```